Structural Engineering Business Card

Brookvane Drafting does residential house plans for clients in Central Florida. Would like simple but elegant business card that is appropriate for a house plan engineering company. Prefer black business card with black/white them but open to other shades of blue. I uploaded a sample card that I came across that looked good but please come up with your own creative designs.

Contact Information for Business Card

Name, Title, Phone, Email, Address, website

```html
<!DOCTYPE html>
<html lang="en">
<head>
<meta charset="utf-8">
<title>Brookvane Drafting — Business Card</title>
<link href="https://fonts.googleapis.com/css2?family=Mulish:wght@400;700;900&display=swap" rel="stylesheet">
<style>
  :root {
    --page: #5f5f5f;
    --navy: #1b1060;
    --navy-line: #3a2f95;
    --black: #050505;
    --ink-line: #2a2a2a;
    --white: #ffffff;
    --soft: #cfcfcf;
    --rule: #8a8a8a;
  }
  * { box-sizing: border-box; margin: 0; padding: 0; }
  html, body { width: 1200px; height: 900px; overflow: hidden; }
  body {
    background: var(--page);
    font-family: "Mulish", sans-serif;
    position: relative;
  }
  .card {
    position: absolute;
    width: 600px;
    height: 343px;
    border-radius: 30px 6px 30px 6px;
    overflow: hidden;
    box-shadow: 0 14px 30px rgba(0,0,0,.45);
  }
  .card--front { left: 150px; top: 70px; background: var(--navy); }
  .card--back  { left: 450px; top: 480px; background: var(--black); }

  .blueprint-area {
    position: absolute;
  }
  .card--front .blueprint-area {
    right: 0; top: 0; width: 330px; height: 100%;
    background: linear-gradient(110deg, rgba(58,47,149,0) 0%, rgba(58,47,149,.55) 60%, rgba(70,58,170,.7) 100%);
  }
  .card--back .blueprint-area {
    left: 0; bottom: 0; width: 380px; height: 220px;
    background: linear-gradient(200deg, rgba(42,42,42,0) 0%, rgba(42,42,42,.7) 55%, rgba(50,50,50,.85) 100%);
  }

  .wordmark {
    position: absolute;
    display: flex;
    align-items: center;
    gap: 12px;
    color: var(--white);
    font-weight: 900;
    letter-spacing: .5px;
    line-height: 1;
    text-transform: uppercase;
  }
  .wordmark__square {
    width: 22px; height: 22px; background: var(--white);
  }
  .card--front .wordmark { left: 44px; top: 150px; font-size: 34px; }
  .card--back .wordmark { right: 40px; top: 222px; font-size: 32px; }

  .person {
    position: absolute; left: 40px; top: 58px; color: var(--white);
  }
  .person__name { font-size: 15px; font-weight: 700; letter-spacing: 1.5px; }
  .person__title { font-size: 14px; color: var(--soft); margin-top: 4px; }

  .contact {
    position: absolute; left: 315px; top: 30px;
    list-style: none; color: var(--white); font-size: 15px;
  }
  .contact li { display: flex; align-items: center; gap: 9px; height: 25px; }
  .contact svg { width: 14px; height: 14px; fill: var(--white); flex: none; }

  .rule {
    position: absolute; right: 0; width: 250px; height: 1px; background: var(--rule);
  }
  .rule--top { top: 140px; width: 270px; }
  .rule--bottom { top: 290px; right: 60px; width: 240px; }
</style>
</head>
<body>

  <section class="card card--front" aria-label="Card front">
    <div class="blueprint-area" role="img" aria-label="Faint blueprint elevation drawing of a house with dimension lines"></div>
    <div class="wordmark"><span class="wordmark__square"></span>Brookvane Drafting</div>
  </section>

  <section class="card card--back" aria-label="Card back">
    <div class="blueprint-area" role="img" aria-label="Faint blueprint elevation drawing of a house with dimension lines"></div>

    <div class="person">
      <p class="person__name">DANIEL MERCER</p>
      <p class="person__title">Architectural Director</p>
    </div>

    <ul class="contact">
      <li>
        <svg viewBox="0 0 24 24" aria-hidden="true"><path d="M6.6 10.8a15.1 15.1 0 0 0 6.6 6.6l2.2-2.2a1 1 0 0 1 1-.25 11.4 11.4 0 0 0 3.6.57 1 1 0 0 1 1 1V20a1 1 0 0 1-1 1A17 17 0 0 1 3 4a1 1 0 0 1 1-1h3.5a1 1 0 0 1 1 1c0 1.25.2 2.45.57 3.57a1 1 0 0 1-.25 1z"/></svg>
        407-555-0182
      </li>
      <li>
        <svg viewBox="0 0 24 24" aria-hidden="true"><path d="M2 5h20v14H2z M4 7v.5l8 5 8-5V7l-8 5z" fill-rule="evenodd"/></svg>
        info@brookvanedrafting.com
      </li>
      <li>
        <svg viewBox="0 0 24 24" aria-hidden="true"><path d="M12 2a10 10 0 1 0 0 20 10 10 0 0 0 0-20zm0 2c1.2 1.4 2 3.5 2.2 7H9.8C10 7.5 10.8 5.4 12 4zm-2.2 9h4.4c-.2 3.5-1 5.6-2.2 7-1.2-1.4-2-3.5-2.2-7zM4.1 11a8 8 0 0 1 4-6.1c-.8 1.6-1.2 3.7-1.3 6.1zm0 2h2.7c.1 2.4.5 4.5 1.3 6.1a8 8 0 0 1-4-6.1zm15.8 0a8 8 0 0 1-4 6.1c.8-1.6 1.2-3.7 1.3-6.1zm0-2h-2.7c-.1-2.4-.5-4.5-1.3-6.1a8 8 0 0 1 4 6.1z"/></svg>
        www.brookvanedrafting.com
      </li>
      <li>
        <svg viewBox="0 0 24 24" aria-hidden="true"><path d="M12 2a7 7 0 0 0-7 7c0 5.2 7 13 7 13s7-7.8 7-13a7 7 0 0 0-7-7zm0 9.5A2.5 2.5 0 1 1 12 6.5a2.5 2.5 0 0 1 0 5z"/></svg>
        18 Cedar Row, Orlando FL 32801
      </li>
    </ul>

    <span class="rule rule--top"></span>
    <div class="wordmark"><span class="wordmark__square"></span>Brookvane Drafting</div>
    <span class="rule rule--bottom"></span>
  </section>

</body>
</html>
```